Business card design needed

Family General Practitioner/ Family Physician.
Logo is the logo of the Noble Guild of Family Healers Oceania
http://kpltw.varendo.example/ImageShelf/marks/pages/NGFHO%20mark_jpg.htm
Updates

Project Deadline Extended
Reason: Just a bit more time to make changes and the weekend for me to look at things closely and to choose. Thanks, Orin

Thanks for all the submissions. So many of them are really works of art. Not one of them are not good. The ones that I am eliminating are the ones that I think are not suitable for me personally only, and because if I don't, it makes it very difficult to decide as many of you are also sending me slight variations of a card. I have just decided to choose a second place card too. Can't thank you all enough. Good luck, Orin. P.S - Working today till 10 pm as the card says :-), so probably won't be able to give a feedback till late Saturday night or Sunday morning here in Sydney, Australia. 

Project Deadline Extended
Reason: Just added a second place to the budget and realised that Australia is ahead of the rest of the world in the time zone (only :-) - don't want to offend anyone or start a debate!! ) , so Monday deadline will mean it will be a weekend for the rest of the world. Just wanted to give everyone more time to submit their best, especially since I will be picking a second card too. Can't thank everyone enough for the submissions. P.S - Not keen on photos on the card.

Industry/Entity Type

Business

Contact Information for Business Card

Dr. Orin Halvey M.B.B.S., F.N.G.F.H.O
Family General Practitioner
Address, timings, phone and fax number on the back.

Requirements
Must have
• Timings
Mon 7 am - 7 pm
Tues 7 am - 12 pm
Wed 7 am - 10 pm
Thurs 7 am - 12 pm
Fri 7 am - 8 pm
Sat 8 am - 10 pm
Sun - Off

```html
<!DOCTYPE html>
<html lang="en">
<head>
<meta charset="utf-8">
<title>Dr. Orin Halvey – Business Card Options</title>
<link rel="stylesheet" href="https://fonts.googleapis.com/css2?family=Cinzel:wght@400;500&family=Tinos:wght@400;700&family=Open+Sans:wght@400;700;800&display=swap">
<style>
  :root {
    --backdrop: #b4875a;
    --card-black: #000000;
    --brand-blue: #2d5cae;
    --accent-red: #e0201c;
    --ink-white: #ffffff;
    --ink-soft: #e8e8e8;
    --mark-faint: #262626;
  }
  html, body {
    margin: 0;
    padding: 0;
    width: 1200px;
    height: 739px;
    overflow: hidden;
    background: var(--backdrop);
  }
  .canvas {
    position: relative;
    width: 1200px;
    height: 739px;
  }
  .card {
    position: absolute;
    width: 525px;
    height: 300px;
    background: var(--card-black);
    overflow: hidden;
    box-shadow: 0 3px 8px rgba(0,0,0,0.35);
  }
  .card--front { left: 35px; top: 27px; }
  .card--opt1 { left: 615px; top: 27px; }
  .card--opt2 { left: 47px; top: 368px; }
  .card--opt3 { left: 612px; top: 375px; }

  /* Front */
  .front-wave { position: absolute; left: 0; top: 0; }
  .doctor-name {
    position: absolute;
    top: 44px; left: 0; width: 525px;
    margin: 0;
    text-align: center;
    font-family: "Cinzel", serif;
    font-weight: 400;
    font-size: 42px;
    letter-spacing: 2px;
    color: var(--ink-white);
    line-height: 1;
  }
  .credentials {
    position: absolute;
    top: 98px; left: 0; width: 525px;
    text-align: center;
    font-family: "Tinos", serif;
    font-size: 11px;
    letter-spacing: 1px;
    color: var(--ink-soft);
  }
  .role {
    position: absolute;
    top: 143px; left: 0; width: 525px;
    text-align: center;
    font-family: "Tinos", serif;
    font-size: 19px;
    letter-spacing: 2px;
    color: var(--ink-white);
  }
  .tagline {
    position: absolute;
    top: 256px; left: 123px;
    font-family: "Tinos", serif;
    font-weight: 700;
    font-size: 22px;
    color: var(--ink-white);
  }
  .guild-mark {
    position: absolute;
    right: 10px; top: 214px;
    width: 92px;
    display: flex;
    align-items: center;
    gap: 4px;
  }
  .guild-mark__dot {
    flex: none;
    width: 12px; height: 12px;
    border-radius: 50%;
    background: var(--ink-white);
  }
  .guild-mark__name {
    font-family: "Tinos", serif;
    font-size: 10px;
    line-height: 1.15;
    color: var(--ink-white);
  }

  /* Back */
  .hours-title {
    position: absolute;
    font-family: "Open Sans", sans-serif;
    font-weight: 400;
    font-size: 20px;
    color: var(--ink-white);
    margin: 0;
  }
  .hours {
    position: absolute;
    margin: 0; padding: 0;
    list-style: none;
    font-family: "Open Sans", sans-serif;
    color: var(--ink-white);
  }
  .hours li { white-space: pre; }
  .card--opt1 .hours-title { left: 38px; top: 16px; }
  .card--opt1 .hours { left: 38px; top: 47px; font-size: 16px; font-weight: 700; line-height: 23px; }
  .card--opt2 .hours-title { left: 50px; top: 6px; letter-spacing: 1px; }
  .card--opt2 .hours { left: 31px; top: 42px; font-size: 16px; line-height: 23.5px; }
  .card--opt2 .hours li { display: flex; }
  .card--opt2 .hours .day { width: 110px; }
  .card--opt2 .hours .time { font-weight: 700; }
  .card--opt3 .hours-title { left: 37px; top: 17px; }
  .card--opt3 .hours { left: 37px; top: 46px; font-size: 16px; line-height: 23px; }
  .card--opt3 .hours .time { font-weight: 700; }

  .faint-mark {
    position: absolute;
    right: 40px; top: 40px;
    width: 180px; height: 150px;
    display: flex;
    align-items: center;
    justify-content: center;
    text-align: center;
    font-family: "Tinos", serif;
    font-size: 20px;
    line-height: 1.2;
    color: var(--mark-faint);
  }
  .card--opt1 .faint-mark { color: #3a3a3a; }

  .back-band {
    position: absolute;
    left: 0; bottom: 0;
    width: 525px; height: 76px;
    background: var(--brand-blue);
    border-top: 2px solid var(--accent-red);
    box-shadow: 0 -3px 0 var(--card-black);
    text-align: center;
    font-family: "Tinos", serif;
    color: var(--ink-white);
  }
  .address { margin: 6px 0 0; font-size: 15px; line-height: 18px; }
  .contact { margin: 9px 0 0; font-size: 15px; }
  .contact .sep { display: inline-block; width: 1px; height: 16px; background: var(--ink-white); vertical-align: -3px; margin: 0 8px; }

  .option-label {
    position: absolute;
    font-family: "Open Sans", sans-serif;
    font-weight: 800;
    font-size: 20px;
    color: var(--ink-white);
    text-shadow: 1px 1px 2px rgba(0,0,0,0.5);
    margin: 0;
  }
  .option-label--1 { left: 823px; top: 338px; }
  .option-label--2 { left: 254px; top: 679px; }
  .option-label--3 { left: 819px; top: 687px; }
</style>
</head>
<body>
<main class="canvas">

  <section class="card card--front" aria-label="Card front">
    <svg class="front-wave" width="525" height="300" viewBox="0 0 525 300" aria-hidden="true">
      <path d="M0,150 C40,205 120,232 250,225 C370,218 450,186 525,182 L525,300 L0,300 Z" fill="var(--brand-blue)"/>
      <path d="M0,160 C50,215 140,238 260,232 C380,224 455,198 525,194 L525,206 C455,212 380,238 260,246 C140,252 50,232 0,178 Z" fill="var(--card-black)"/>
      <path d="M0,178 C50,232 140,252 260,246 C380,238 455,212 525,206 L525,212 C455,220 380,246 260,254 C140,260 50,242 0,190 Z" fill="var(--accent-red)"/>
      <path d="M0,190 C50,242 140,260 260,254 C380,246 455,220 525,212 L525,216 C455,226 380,252 260,260 C140,266 50,250 0,198 Z" fill="var(--card-black)"/>
    </svg>
    <h1 class="doctor-name">Dr. Orin Halvey</h1>
    <div class="credentials">M.B.B.S., F.N.G.F.H.O</div>
    <div class="role">Family General Practitioner</div>
    <div class="tagline">Caring about your health</div>
    <div class="guild-mark">
      <span class="guild-mark__dot"></span>
      <span class="guild-mark__name">Noble Guild of Family Healers Oceania</span>
    </div>
  </section>

  <section class="card card--opt1" aria-label="Card back, option 1">
    <div class="faint-mark">Noble Guild of Family Healers Oceania</div>
    <h2 class="hours-title">Working Hours</h2>
    <ul class="hours">
      <li>MONDAY  7 AM  - 7 PM</li>
      <li>TUESDAY  7 AM - 12 PM</li>
      <li>WEDNESDAY  7 AM - 10 PM</li>
      <li>THURSDAY  7 AM - 12 PM</li>
      <li>FRIDAY   7 AM  - 8 PM</li>
      <li>SATURDAY  8 AM - 10 PM</li>
      <li>SUNDAY - OFF</li>
    </ul>
    <div class="back-band">
      <p class="address">Upper Level, Linden Arcade, Brookvale Plaza Centre<br>Fernhurst, NSW 2199</p>
      <p class="contact">P: 02 8015 3700<span class="sep"></span>F: 02 8015 3711</p>
    </div>
  </section>

  <section class="card card--opt2" aria-label="Card back, option 2">
    <div class="faint-mark">Noble Guild of Family Healers Oceania</div>
    <h2 class="hours-title">Working Hours</h2>
    <ul class="hours">
      <li><span class="day">Monday</span><span class="time">7 AM   - 7 PM</span></li>
      <li><span class="day">Tuesday</span><span class="time">7 AM - 12 PM</span></li>
      <li><span class="day">Wednesday</span><span class="time">7 AM - 10 PM</span></li>
      <li><span class="day">Thursday</span><span class="time">7 AM - 12 PM</span></li>
      <li><span class="day">Friday</span><span class="time">7 AM   - 8 PM</span></li>
      <li><span class="day">Saturday</span><span class="time">8 AM - 10 PM</span></li>
      <li><span class="day">Sunday</span><span class="time">OFF</span></li>
    </ul>
    <div class="back-band">
      <p class="address">Upper Level, Linden Arcade, Brookvale Plaza Centre<br>Fernhurst, NSW 2199</p>
      <p class="contact">P: 02 8015 3700<span class="sep"></span>F: 02 8015 3711</p>
    </div>
  </section>

  <section class="card card--opt3" aria-label="Card back, option 3">
    <div class="faint-mark">Noble Guild of Family Healers Oceania</div>
    <h2 class="hours-title">Working Hours</h2>
    <ul class="hours">
      <li>Monday  <span class="time">7 AM   - 7 PM</span></li>
      <li>Tuesday  <span class="time">7 AM - 12 PM</span></li>
      <li>Wednesday  <span class="time">7 AM - 10 PM</span></li>
      <li>Thursday  <span class="time">7 AM - 12 PM</span></li>
      <li>Friday   <span class="time">7 AM   - 8 PM</span></li>
      <li>Saturday  <span class="time">8 AM - 10 PM</span></li>
      <li>Sunday - <span class="time">OFF</span></li>
    </ul>
    <div class="back-band">
      <p class="address">Upper Level, Linden Arcade, Brookvale Plaza Centre<br>Fernhurst, NSW 2199</p>
      <p class="contact">P: 02 8015 3700<span class="sep"></span>F: 02 8015 3711</p>
    </div>
  </section>

  <p class="option-label option-label--1">Option# 1</p>
  <p class="option-label option-label--2">Option# 2</p>
  <p class="option-label option-label--3">Option# 3</p>

</main>
</body>
</html>
```